Blind Rivet Product catalogue

Need a design in wordpress with a productcatalogue where i present all products. This is a B2B business. The products is Blindrivets and Blindrivet nuts and accessories to this. I only want the basic information and also technical specification.

This is a subcompany to my existing company k7.m3.se but specializing in a subcategory

Businesses using blind rivet technology.

Industrial

Sans Serif

Must have
• Three different categories for the products; Blind Rivets - Blind Rivet Nut - Riveting Tools
Nice to have
• Possible to ad login for more information of the different sizes

```html
<!DOCTYPE html>
<html lang="en">
<head>
<meta charset="utf-8">
<title>K7M3 – Blind Rivet Catalogue</title>
<link href="https://fonts.googleapis.com/css2?family=Lato:ital,wght@0,400;0,700;1,400&family=Montserrat:wght@500;600;700;800&display=swap" rel="stylesheet">
<style>
:root{
  --green:#7dc142;
  --red:#e8262b;
  --black:#000;
  --ink:#1a1a1a;
  --muted:#666;
  --star:#f5a623;
  --footer:#333333;
  --line:#e6e6e6;
  --white:#fff;
}
*{box-sizing:border-box;margin:0;padding:0}
html,body{width:1200px;height:2878px;overflow:hidden}
body{position:relative;font-family:'Lato',sans-serif;color:var(--ink);background:var(--white)}
.abs{position:absolute}
a{color:inherit;text-decoration:none}

.site-header{left:0;top:0;width:1200px;height:86px;background:var(--black)}
.brand{left:113px;top:28px;display:flex;align-items:center;gap:8px;color:var(--white);font:700 24px 'Lato',sans-serif;letter-spacing:1px}
.brand-square{width:14px;height:14px;background:var(--green)}
.main-nav{left:276px;top:34px;display:flex;gap:31px;font:700 14.5px 'Lato',sans-serif;color:var(--white)}
.main-nav .active{color:var(--red)}
.cart{left:860px;top:23px;width:40px;height:40px;border:2px solid var(--white);border-radius:50%;display:flex;align-items:center;justify-content:center}
.cart-count{left:891px;top:15px;width:24px;height:24px;border-radius:50%;background:var(--green);color:var(--white);font:400 15px 'Lato',sans-serif;display:flex;align-items:center;justify-content:center}
.login{left:974px;top:20px;width:115px;height:46px;background:var(--green);color:var(--white);font:700 14.5px 'Lato',sans-serif;display:flex;align-items:center;justify-content:center;gap:8px}

.hero{left:0;top:86px;width:1200px;height:558px;background:linear-gradient(110deg,#8a6a4c 0%,#b89a78 35%,#d8c3a8 55%,#9a7b5c 80%,#6e5640 100%)}
.hero-title{left:107px;top:250px;font:800 70px 'Montserrat',sans-serif;color:var(--white);letter-spacing:1px}
.hero-text{left:111px;top:342px;width:480px;font:400 14.5px/24px 'Lato',sans-serif;color:var(--white)}
.hero-cta{left:112px;top:412px;width:148px;height:49px;background:var(--green);color:var(--white);font:700 14.5px 'Lato',sans-serif;display:flex;align-items:center;justify-content:center;gap:8px}
.dots{left:1137px;top:324px;display:flex;flex-direction:column;gap:9px}
.dots span{width:9px;height:9px;border-radius:50%;background:var(--white)}
.dots .current{background:transparent;border:2px solid var(--white)}

.section-title{left:0;width:1200px;text-align:center;font:500 36px 'Montserrat',sans-serif;color:var(--ink)}
.section-lead{left:250px;width:700px;text-align:center;font:400 15px/25px 'Lato',sans-serif;color:var(--muted)}

.category{top:875px;width:254px;height:103px;background:var(--white);box-shadow:0 1px 6px rgba(0,0,0,.18);display:flex;align-items:center}
.category svg{flex:none}
.category-name{font:700 16px 'Montserrat',sans-serif;color:var(--ink);margin-left:auto;margin-right:22px}

.product{top:1180px;width:318px;height:392px;background:var(--white);box-shadow:0 1px 8px rgba(0,0,0,.15);text-align:center}
.product-image{position:absolute;left:84px;top:30px;width:150px;height:130px;border-radius:6px}
.product-title{position:absolute;left:0;width:100%;top:205px;font:600 16.5px 'Montserrat',sans-serif;letter-spacing:.5px}
.product-price{position:absolute;left:0;width:100%;top:233px;font:700 31px 'Montserrat',sans-serif;color:var(--green)}
.product-stars{position:absolute;left:0;width:100%;top:282px}
.add-cart{position:absolute;left:86px;top:320px;width:148px;height:46px;border:2px solid var(--green);color:var(--green);font:700 14px 'Lato',sans-serif;display:flex;align-items:center;justify-content:center;gap:8px}
.add-cart.filled{background:var(--green);color:var(--white)}

.about-title{left:112px;top:1668px;font:500 35px 'Montserrat',sans-serif}
.about-intro{left:112px;top:1725px;width:282px;font:400 15px/24px 'Lato',sans-serif;color:var(--muted);text-align:justify}
.about-divider{left:447px;top:1672px;width:12px;height:184px}
.about-body{left:503px;top:1684px;width:582px;font:400 15px/26.5px 'Lato',sans-serif;color:var(--muted);text-align:justify}

.testimonial-band{left:0;top:1953px;width:1200px;height:535px;background:linear-gradient(180deg,#d6d7d9 0%,#eeeeef 45%,#dcdcde 80%,#cfd0d2 100%)}
.quote{top:2150px;width:317px;height:202px;background:var(--white);text-align:center;padding:0 20px}
.quote p{font:italic 400 14.5px/30px 'Lato',sans-serif;color:#555}
.avatar{left:562px;top:2112px;width:76px;height:76px;border-radius:50%;background:radial-gradient(circle at 50% 40%,#d8d0c8,#9a9490);border:3px solid #e9e9e9}
.quote-pointer{left:582px;top:2351px}
.person{top:2386px;width:317px;text-align:center}
.person-name{font:700 22px 'Montserrat',sans-serif;color:var(--ink);letter-spacing:.5px}
.person-role{font:600 15px 'Montserrat',sans-serif;color:var(--ink);margin-top:4px}
.slider-arrow{top:2208px;width:52px;height:52px;border-radius:50%;background:var(--white);box-shadow:0 1px 6px rgba(0,0,0,.2);display:flex;align-items:center;justify-content:center}

.site-footer{left:0;top:2488px;width:1200px;height:390px;background:var(--footer)}
.footer-heading{top:2563px;font:700 14.5px 'Lato',sans-serif;color:var(--white)}
.footer-heading::after{content:"";display:block;width:24px;height:3px;background:var(--white);margin-top:10px}
.footer-list{top:2608px;list-style:none;font:400 15px 'Lato',sans-serif;color:var(--white)}
.footer-list li{height:34.5px;display:flex;align-items:center;gap:16px}
.footer-list svg{flex:none}
.footer-rule{left:112px;top:2810px;width:976px;height:1px;background:#8a8a8a}
.copyright{left:0;top:2832px;width:1200px;text-align:center;font:400 15px 'Lato',sans-serif;color:var(--white)}
</style>
</head>
<body>
<svg width="0" height="0" style="position:absolute">
  <defs>
    <symbol id="star" viewBox="0 0 20 20"><polygon points="10,1 12.6,7 19,7.4 14,11.6 15.6,18 10,14.5 4.4,18 6,11.6 1,7.4 7.4,7" fill="var(--star)"/></symbol>
    <symbol id="chev" viewBox="0 0 12 12"><path d="M2 2l4 4-4 4M6 2l4 4-4 4" fill="none" stroke="#fff" stroke-width="1.6"/></symbol>
    <symbol id="cart-icon" viewBox="0 0 16 14"><path d="M0 1h3l2 8h8l2-6H4" fill="none" stroke="currentColor" stroke-width="2"/><circle cx="6" cy="12" r="1.4" fill="currentColor"/><circle cx="12" cy="12" r="1.4" fill="currentColor"/></symbol>
  </defs>
</svg>

<header class="abs site-header">
  <div class="abs brand"><span class="brand-square"></span>K7M3</div>
  <nav class="abs main-nav">
    <a class="active">HOME</a><a>ABOUT US</a><a>OUR PRODUCTS</a><a>LATEST BLOG</a><a>CONTACTS</a>
  </nav>
  <div class="abs cart" style="color:#fff"><svg width="17" height="15"><use href="#cart-icon"/></svg></div>
  <div class="abs cart-count">0</div>
  <a class="abs login">LOG IN
    <svg width="11" height="13" viewBox="0 0 11 13"><rect x="0" y="5.5" width="11" height="7.5" fill="#fff"/><path d="M2.5 6V4a3 3 0 0 1 6 0v2" fill="none" stroke="#fff" stroke-width="1.8"/></svg>
  </a>
</header>

<section class="abs hero" role="img" aria-label="Hand driving a screw into a wooden board with a screwdriver"></section>
<h1 class="abs hero-title">BLIND RIVET</h1>
<p class="abs hero-text">Sed ut perspiciatis unde omnis iste natus error sit voluptatem accusantium doloremque laudantium, totam rem aperiam.</p>
<a class="abs hero-cta">GET STARTED
  <svg width="14" height="14" viewBox="0 0 14 14"><circle cx="7" cy="7" r="7" fill="#fff"/><path d="M5.5 4l3 3-3 3" fill="none" stroke="var(--green)" stroke-width="2"/></svg>
</a>
<div class="abs dots"><span></span><span></span><span class="current"></span><span></span><span></span></div>

<h2 class="abs section-title" style="top:710px">Categories</h2>
<p class="abs section-lead" style="top:773px">Lorem ipsum dolor sit amet, consectetur adipiscing elit, sed do eiusmod tempor incididunt ut labore et dolore magna aliqua t enim ad minim veniam</p>

<div class="abs category" style="left:195px">
  <svg width="78" height="103" role="img" aria-label="Blind rivets icon"><path d="M0 0h48q30 51 0 103H0z" fill="var(--red)"/></svg>
  <span class="category-name">BLIND RIVETS</span>
</div>
<div class="abs category" style="left:474px">
  <svg width="78" height="103" role="img" aria-label="Blind rivet nut icon"><path d="M0 0h48q30 51 0 103H0z" fill="var(--green)"/></svg>
  <span class="category-name" style="margin-right:10px">BLIND RIVET NUT</span>
</div>
<div class="abs category" style="left:752px">
  <svg width="78" height="103" role="img" aria-label="Riveting tools icon"><path d="M0 0h48q30 51 0 103H0z" fill="var(--red)"/></svg>
  <span class="category-name" style="margin-right:14px">RIVETING TOOLS</span>
</div>

<h2 class="abs section-title" style="top:1085px">Featured Products</h2>

<article class="abs product" style="left:112px">
  <div class="product-image" role="img" aria-label="Cordless riveting tool" style="background:radial-gradient(circle,#cfcfcf 0%,#f4f4f4 70%)"></div>
  <h3 class="product-title">PRODUCT TITLE</h3>
  <div class="product-price">$25.00</div>
  <div class="product-stars"><svg width="84" height="15"><use href="#star" x="0" width="15" height="15"/><use href="#star" x="17" width="15" height="15"/><use href="#star" x="34" width="15" height="15"/><use href="#star" x="51" width="15" height="15"/><use href="#star" x="68" width="15" height="15"/></svg></div>
  <a class="add-cart">ADD TO CART <svg width="14" height="12"><use href="#cart-icon"/></svg></a>
</article>
<article class="abs product" style="left:441px">
  <div class="product-image" role="img" aria-label="Blind rivet nut" style="background:radial-gradient(circle,#c4c4c4 0%,#f4f4f4 70%)"></div>
  <h3 class="product-title">PRODUCT TITLE</h3>
  <div class="product-price">$25.00</div>
  <div class="product-stars"><svg width="84" height="15"><use href="#star" x="0" width="15" height="15"/><use href="#star" x="17" width="15" height="15"/><use href="#star" x="34" width="15" height="15"/><use href="#star" x="51" width="15" height="15"/><use href="#star" x="68" width="15" height="15"/></svg></div>
  <a class="add-cart filled">ADD TO CART <svg width="14" height="12"><use href="#cart-icon"/></svg></a>
</article>
<article class="abs product" style="left:771px">
  <div class="product-image" role="img" aria-label="Blind rivet with mandrel" style="left:64px;width:190px;background:radial-gradient(ellipse,#cdcdcd 0%,#f4f4f4 70%)"></div>
  <h3 class="product-title">PRODUCT TITLE</h3>
  <div class="product-price">$25.00</div>
  <div class="product-stars"><svg width="84" height="15"><use href="#star" x="0" width="15" height="15"/><use href="#star" x="17" width="15" height="15"/><use href="#star" x="34" width="15" height="15"/><use href="#star" x="51" width="15" height="15"/><use href="#star" x="68" width="15" height="15"/></svg></div>
  <a class="add-cart">ADD TO CART <svg width="14" height="12"><use href="#cart-icon"/></svg></a>
</article>

<h2 class="abs about-title">About Us</h2>
<p class="abs about-intro">Lorem ipsum dolor sit amet, consectetur adipiscing elit, sed do eiusmod tempor incididunt ut labore et dolore magna aliqua. Ut enim ad minim veniam, quis nostrud exercitation</p>
<svg class="abs about-divider" viewBox="0 0 12 184"><path d="M1 0v112l8 8-8 8v56" fill="none" stroke="#e3e3e3" stroke-width="1.5"/></svg>
<p class="abs about-body">Sed ut perspiciatis unde omnis iste natus error sit voluptatem accusantium doloremque laudantium, totam rem aperiam, eaque ipsa quae ab illo inventore veritatis et quasi architecto beatae vitae dicta sunt explicabo. Nemo enim ipsam voluptatem quia voluptas sit aspernatur aut odit aut fugit Sed ut perspiciatis unde omnis iste natus error sit voluptatem accusantium doloremque laudantium, totam rem aperiam, eaque ipsa quae ab illo inventore veritatis et quasi architecto beatae vitae dicta sunt explicabo.</p>

<section class="abs testimonial-band" role="img" aria-label="Brushed metal sheet background with rivet heads"></section>
<h2 class="abs section-title" style="top:2035px">Featured Products</h2>

<div class="abs slider-arrow" style="left:28px"><svg width="14" height="20"><path d="M11 2L3 10l8 8" fill="none" stroke="#111" stroke-width="2.6"/></svg></div>
<div class="abs slider-arrow" style="left:1120px"><svg width="14" height="20"><path d="M3 2l8 8-8 8" fill="none" stroke="#111" stroke-width="2.6"/></svg></div>

<blockquote class="abs quote" style="left:112px;padding-top:28px">
  <svg width="106" height="18"><use href="#star" x="0" width="18" height="18"/><use href="#star" x="22" width="18" height="18"/><use href="#star" x="44" width="18" height="18"/><use href="#star" x="66" width="18" height="18"/><use href="#star" x="88" width="18" height="18" opacity=".55"/></svg>
  <p style="margin-top:8px">Sed ut perspiciatis unde omnis iste natus error sit voluptatem accusantium doloremque laudantium, totam aperiam, eaque ipsa quae ab illo inventore. veritatis et quasi architecto</p>
</blockquote>
<blockquote class="abs quote" style="left:441px;padding-top:66px">
  <svg width="106" height="18"><use href="#star" x="0" width="18" height="18"/><use href="#star" x="22" width="18" height="18"/><use href="#star" x="44" width="18" height="18"/><use href="#star" x="66" width="18" height="18"/><use href="#star" x="88" width="18" height="18" opacity=".55"/></svg>
  <p style="margin-top:8px">Sed ut perspiciatis unde omnis iste natus error sit voluptatem accusantium doloremque laudantium, totam.</p>
</blockquote>
<svg class="abs quote-pointer" width="36" height="18"><path d="M0 0h36L18 18z" fill="#fff"/></svg>
<div class="abs avatar" role="img" aria-label="Customer portrait"></div>
<blockquote class="abs quote" style="left:770px;padding-top:28px">
  <svg width="106" height="18"><use href="#star" x="0" width="18" height="18"/><use href="#star" x="22" width="18" height="18"/><use href="#star" x="44" width="18" height="18"/><use href="#star" x="66" width="18" height="18"/><use href="#star" x="88" width="18" height="18" opacity=".55"/></svg>
  <p style="margin-top:8px">Sed ut perspiciatis unde omnis iste natus error sit voluptatem accusantium doloremque laudantium, totam aperiam, eaque ipsa quae ab illo inventore. veritatis et quasi architecto</p>
</blockquote>

<div class="abs person" style="left:112px"><div class="person-name">MARLOW KEATON</div><div class="person-role">Businessman</div></div>
<div class="abs person" style="left:441px"><div class="person-name">OSKAR LINDVALL</div><div class="person-role">Businessman</div></div>
<div class="abs person" style="left:770px"><div class="person-name">TOBIAS RENNER</div><div class="person-role">Businessman</div></div>

<footer class="abs site-footer"></footer>
<h4 class="abs footer-heading" style="left:120px">QUICK LINKS</h4>
<ul class="abs footer-list" style="left:120px">
  <li><svg width="12" height="12"><use href="#chev"/></svg>HOME</li>
  <li><svg width="12" height="12"><use href="#chev"/></svg>About Us</li>
  <li><svg width="12" height="12"><use href="#chev"/></svg>Our Products</li>
  <li><svg width="12" height="12"><use href="#chev"/></svg>Latest Blog</li>
  <li><svg width="12" height="12"><use href="#chev"/></svg>Review</li>
</ul>
<h4 class="abs footer-heading" style="left:376px">OTHER LINKS</h4>
<ul class="abs footer-list" style="left:376px">
  <li><svg width="12" height="12"><use href="#chev"/></svg>FAQ</li>
  <li><svg width="12" height="12"><use href="#chev"/></svg>Terms &amp; Conditions</li>
  <li><svg width="12" height="12"><use href="#chev"/></svg>Privacy Policy</li>
  <li><svg width="12" height="12"><use href="#chev"/></svg>More</li>
  <li><svg width="12" height="12"><use href="#chev"/></svg>Contact Us</li>
</ul>
<h4 class="abs footer-heading" style="left:654px">CONTACT US</h4>
<ul class="abs footer-list" style="left:654px">
  <li><svg width="14" height="16" viewBox="0 0 14 16"><path d="M7 15S1 9 1 6a6 6 0 0 1 12 0c0 3-6 9-6 9z" fill="#fff"/><circle cx="7" cy="6" r="2" fill="var(--footer)"/></svg>Finibus Bonorum</li>
  <li style="padding-left:31px">established fact</li>
  <li><svg width="15" height="15" viewBox="0 0 15 15"><path d="M3 1l3 3-2 2q2 4 5 5l2-2 3 3-2 2Q5 14 1 3z" fill="#fff"/></svg>1 555 010 200</li>
  <li><svg width="15" height="15" viewBox="0 0 15 15"><rect x="1" y="5" width="13" height="9" fill="none" stroke="#fff" stroke-width="1.6"/><rect x="4" y="1" width="7" height="5" fill="none" stroke="#fff" stroke-width="1.6"/></svg>1 555 010 300</li>
  <li><svg width="15" height="12" viewBox="0 0 15 12"><rect x="1" y="1" width="13" height="10" fill="none" stroke="#fff" stroke-width="1.4"/><path d="M1 1l6.5 6L14 1" fill="none" stroke="#fff" stroke-width="1.4"/></svg>info@k7m3.se</li>
</ul>
<h4 class="abs footer-heading" style="left:967px">FIND US ON</h4>
<ul class="abs footer-list" style="left:967px">
  <li><svg width="15" height="15"><circle cx="7.5" cy="7.5" r="6" fill="#fff"/></svg>Newsfeed</li>
  <li><svg width="15" height="15"><circle cx="7.5" cy="7.5" r="6" fill="#fff"/></svg>Photo Wall</li>
  <li><svg width="15" height="15"><circle cx="7.5" cy="7.5" r="6" fill="#fff"/></svg>Community</li>
  <li><svg width="15" height="15"><circle cx="7.5" cy="7.5" r="6" fill="#fff"/></svg>Video Channel</li>
</ul>
<div class="abs footer-rule"></div>
<p class="abs copyright">Copyrights © 2020 K7M3. All Rights Reserved</p>
</body>
</html>
```